Business Cards for a law firm

Business cards for our law firm. Use our silhoette logo and OAK PARTNERS - check our website (www.oakpartners.example)

Contact Information for Business Card

our silhouette logo, OAK PARTNERS, 800-555-0147, Dorian Pemberton, dorian@oakpartners.example

Requirements
Must have
• our silhouette logo, OAK PARTNERS, 800-555-0147, Dorian Pemberton, dorian@oakpartners.example

```html
<!DOCTYPE html>
<html lang="en">
<head>
<meta charset="utf-8">
<title>Oak Partners – Business Cards</title>
<link rel="stylesheet" href="https://fonts.googleapis.com/css2?family=Cinzel:wght@400;600;700&display=swap">
<style>
  :root {
    --backdrop: #8a8a8c;
    --paper: #ffffff;
    --navy: #1f2d6b;
    --navy-card: #223069;
    --ink-light: #ffffff;
    --ink-soft: #dfe3f2;
  }
  * { margin: 0; padding: 0; box-sizing: border-box; }
  html, body { width: 900px; height: 1200px; overflow: hidden; }
  body {
    background: var(--backdrop);
    font-family: "Cinzel", serif;
    position: relative;
  }
  .card {
    position: absolute;
    left: 133px;
    width: 633px;
    height: 364px;
  }
  .card--front { top: 210px; background: var(--paper); }
  .card--back { top: 624px; background: var(--navy-card); color: var(--ink-light); }

  .brand {
    position: absolute;
    left: 72px;
    top: 156px;
    display: flex;
    align-items: center;
    gap: 18px;
  }
  .brand__mark { width: 44px; height: 44px; background: var(--navy); }
  .brand__name {
    color: var(--navy);
    font-weight: 700;
    font-size: 46px;
    letter-spacing: 1px;
    line-height: 1;
  }
  .front__web {
    position: absolute;
    left: 0; right: 0;
    top: 318px;
    text-align: center;
    color: var(--navy);
    font-weight: 700;
    font-size: 12px;
    letter-spacing: 3.5px;
  }

  .back__firm {
    position: absolute;
    left: 40px; top: 44px;
    font-weight: 600;
    font-size: 30px;
    letter-spacing: 1px;
  }
  .person { position: absolute; left: 40px; top: 182px; }
  .person__name { font-weight: 600; font-size: 24px; letter-spacing: 1px; }
  .person__role { font-size: 14px; color: var(--ink-soft); margin-top: 2px; letter-spacing: 0.5px; }
  .contact { list-style: none; margin-top: 16px; }
  .contact__item {
    display: flex; align-items: center; gap: 5px;
    font-size: 12px; letter-spacing: 0.5px; height: 26px;
  }
  .contact__item--phone { font-size: 15px; letter-spacing: 2px; }
  .contact__icon { width: 14px; height: 14px; fill: var(--ink-light); stroke: var(--ink-light); }
</style>
</head>
<body>
  <section class="card card--front">
    <div class="brand">
      <span class="brand__mark"></span>
      <span class="brand__name">OAK PARTNERS</span>
    </div>
    <p class="front__web">WWW.OAKPARTNERS.EXAMPLE</p>
  </section>

  <section class="card card--back">
    <h1 class="back__firm">OAK PARTNERS</h1>
    <div class="person">
      <h2 class="person__name">DORIAN PEMBERTON</h2>
      <p class="person__role">ATTORNEY</p>
      <ul class="contact">
        <li class="contact__item contact__item--phone">
          <svg class="contact__icon" viewBox="0 0 16 16" aria-hidden="true"><path stroke="none" d="M3 1l3 3-1.5 2c1 2 3 4 5 5L11.5 9.5l3 3-2 2.5C7 14 2 9 1 3z"/></svg>
          800-555-0147
        </li>
        <li class="contact__item">
          <svg class="contact__icon" viewBox="0 0 16 16" aria-hidden="true"><rect x="1" y="3" width="14" height="10" stroke="none"/><path d="M1 3l7 6 7-6" fill="none" stroke="#223069" stroke-width="1.4"/></svg>
          DORIAN@OAKPARTNERS.EXAMPLE
        </li>
        <li class="contact__item">
          <svg class="contact__icon" viewBox="0 0 16 16" aria-hidden="true" fill="none" stroke-width="1.2"><circle cx="8" cy="8" r="6.5" fill="none"/><ellipse cx="8" cy="8" rx="3" ry="6.5" fill="none"/><path d="M1.5 8h13M2.5 5h11M2.5 11h11"/></svg>
          WWW.OAKPARTNERS.EXAMPLE
        </li>
      </ul>
    </div>
  </section>
</body>
</html>
```